Birchline Septic Solutions

Would like to see some single sided ones but would also like to see some double sided with one sided only being the logo. Owners name is Colin Vandro. Phone number is 555-214-0387
Services are pumping, inspections, installs, and repairs

Contact Information for Business Card

555-241-0387 Colin Vandro Lindenvale, KY

```html
<!DOCTYPE html>
<html lang="en">
<head>
<meta charset="utf-8">
<title>Birchline Septic Solutions – Business Cards</title>
<link href="https://fonts.googleapis.com/css2?family=Montserrat:wght@400;500;800&display=swap" rel="stylesheet">
<style>
  :root {
    --page: #2a2a2a;
    --ink: #0a0a0a;
    --paper: #ffffff;
    --teal: #2bbdb5;
    --text-dark: #141414;
  }
  * { box-sizing: border-box; margin: 0; padding: 0; }
  html, body {
    width: 1200px; height: 880px; overflow: hidden;
    background: var(--page);
    font-family: "Montserrat", Arial, sans-serif;
  }
  .card {
    position: absolute; left: 285px;
    width: 630px; height: 360px;
    overflow: hidden;
    box-shadow: 0 12px 30px rgba(0,0,0,.45);
  }
  .card--back { top: 60px; background: var(--ink); color: var(--paper); }
  .card--front { top: 460px; background: var(--paper); color: var(--text-dark); }

  .wordmark {
    font-weight: 800; text-transform: uppercase; line-height: 1.05;
    text-align: center; white-space: nowrap;
  }
  .card--back .wordmark {
    position: absolute; top: 78px; left: 0; right: 0;
    font-size: 46px; letter-spacing: 2px; color: var(--paper);
  }
  .wordmark .sub { display: block; font-size: 18px; letter-spacing: 7px; margin-top: 6px; }

  .services {
    position: absolute; top: 222px; left: 0; right: 0;
    text-align: center; font-size: 19px; font-weight: 400; line-height: 1.45;
  }
  .tick {
    display: inline-block; width: 14px; height: 14px; vertical-align: -1px;
    margin: 0 6px 0 4px;
  }

  .card--front .wordmark {
    position: absolute; left: 34px; top: 120px; width: 270px;
    font-size: 36px; letter-spacing: 1px; color: var(--text-dark);
  }
  .card--front .wordmark .sub { font-size: 14px; letter-spacing: 5px; }

  .divider {
    position: absolute; left: 316px; top: 76px; width: 2px; height: 132px;
    background: var(--teal);
  }
  .contact { position: absolute; left: 336px; top: 70px; width: 280px; }
  .contact__name { font-size: 25px; font-weight: 800; letter-spacing: -.3px; text-transform: uppercase; white-space: nowrap; }
  .contact__name .surname { color: var(--teal); }
  .contact__role { font-size: 14px; font-weight: 500; margin: 2px 0 12px 10px; }
  .contact__line {
    display: flex; align-items: center; gap: 8px;
    font-size: 15px; font-weight: 500; margin: 0 0 6px 20px; white-space: nowrap;
  }
  .contact__line svg { width: 16px; height: 16px; fill: var(--teal); flex: none; }
  .footer-bands { position: absolute; left: 0; top: 0; width: 630px; height: 360px; }
</style>
</head>
<body>

<section class="card card--back" aria-label="Card back">
  <div class="wordmark">Birchline<span class="sub">Septic Solutions</span></div>
  <p class="services">
    <svg class="tick" viewBox="0 0 14 14"><circle cx="7" cy="7" r="6" fill="none" stroke="#fff" stroke-width="1.5"/><path d="M4 7.2l2 2 4-4.4" fill="none" stroke="#fff" stroke-width="1.6"/></svg>Services are pumping<br>
    <svg class="tick" viewBox="0 0 14 14"><circle cx="7" cy="7" r="6" fill="none" stroke="#fff" stroke-width="1.5"/><path d="M4 7.2l2 2 4-4.4" fill="none" stroke="#fff" stroke-width="1.6"/></svg>inspections
    <svg class="tick" viewBox="0 0 14 14"><circle cx="7" cy="7" r="6" fill="none" stroke="#fff" stroke-width="1.5"/><path d="M4 7.2l2 2 4-4.4" fill="none" stroke="#fff" stroke-width="1.6"/></svg>installs
    <svg class="tick" viewBox="0 0 14 14"><circle cx="7" cy="7" r="6" fill="none" stroke="#fff" stroke-width="1.5"/><path d="M4 7.2l2 2 4-4.4" fill="none" stroke="#fff" stroke-width="1.6"/></svg>and repairs
  </p>
</section>

<section class="card card--front" aria-label="Card front">
  <svg class="footer-bands" viewBox="0 0 630 360" aria-hidden="true">
    <polygon points="0,346 250,346 244,356 0,356" fill="var(--teal)"/>
    <polygon points="254,360 262,342 370,342 362,360" fill="var(--ink)"/>
    <polygon points="372,360 380,336 536,336 546,300 630,290 630,360" fill="var(--ink)"/>
    <polygon points="380,330 534,330 540,316 386,316" fill="var(--teal)"/>
  </svg>
  <div class="wordmark">Birchline<span class="sub">Septic Solutions</span></div>
  <div class="divider"></div>
  <div class="contact">
    <h1 class="contact__name">Colin <span class="surname">Vandro</span></h1>
    <p class="contact__role">Owners</p>
    <p class="contact__line">
      <svg viewBox="0 0 16 16"><path d="M3 2h3l1.5 3.5-2 1.3a8 8 0 0 0 3.7 3.7l1.3-2L14 10v3a1.5 1.5 0 0 1-1.5 1.5A11.5 11.5 0 0 1 1.5 3.5 1.5 1.5 0 0 1 3 2z"/></svg>
      555-214-0387
    </p>
    <p class="contact__line">
      <svg viewBox="0 0 16 16"><path d="M8 1a5 5 0 0 0-5 5c0 3.8 5 9 5 9s5-5.2 5-9a5 5 0 0 0-5-5zm0 7a2 2 0 1 1 0-4 2 2 0 0 1 0 4z"/></svg>
      Colin Vandro Lindenvale, KY
    </p>
  </div>
</section>

</body>
</html>
```